i would like a business card to leave with customers and potential customers for electrical work and for the supply and install of reverse cycle airconditioning in the domestic and commercial market.
I own my own business and im a sole trader. I have an a'class electrical lisence and also a refrigeration lisence so i am
able to offer complete installations in airconditioning by a fully qualified and lisenced tradesman.
im looking for something that comes across as unique and professional.
i had the coluor black and some gold in mind but open to any coluors.
something like Lanterra Electrical & Refrigeration
or Lanterra Air.
i will use this design on a business card to advertise through summer to help generate installs through the busy season.

Target Market(s)

Mainly domestic house holds through summer who are in need of airconditioning and reliable information to acomadate thier cooling and heating requirements

Industry/Entity Type

Electrical

Requirements
Must have
• Business name- Lanterra
My name- Mark Delford
My mobile no- 0438 517 290
My email- mrdelford@qelvo.com.au
Installation & Decomissioning of aiconditioning split systems
LIC NO: TRK 540316
Nice to have
• Lanterra Electrical & Refrigeration

```html
<!DOCTYPE html>
<html lang="en">
<head>
<meta charset="utf-8">
<title>Lanterra Electrical – Business Card</title>
<link href="https://fonts.googleapis.com/css2?family=Crimson+Pro:wght@400&family=Tenor+Sans&display=swap" rel="stylesheet">
<style>
  :root {
    --backdrop: #3d4b4b;
    --card-dark: #161616;
    --card-mid: #2c2c2c;
    --card-light: #3a3a3a;
    --brand-blue: #3a9fd8;
    --swoosh-blue: #2a72c0;
    --name-grey: #cfcfcf;
    --label-grey: #8a8a8a;
    --value-grey: #dedede;
    --badge-white: #f4f4f4;
  }
  * { margin: 0; padding: 0; box-sizing: border-box; }
  html, body { width: 1200px; height: 750px; overflow: hidden; }
  body {
    position: relative;
    background: var(--backdrop);
    font-family: "Crimson Pro", Georgia, serif;
  }

  .brand-showcase {
    position: absolute;
    left: 200px; top: 120px;
    width: 320px; height: 140px;
    display: flex; align-items: center; justify-content: center; gap: 18px;
  }
  .brand-mark-dot {
    width: 34px; height: 34px; border-radius: 50%;
    background: var(--brand-blue);
  }
  .brand-wordmark {
    font-family: "Tenor Sans", "Helvetica Neue", sans-serif;
    font-size: 54px; color: var(--brand-blue); letter-spacing: 2px;
  }

  .card {
    position: absolute;
    width: 530px; height: 324px;
    overflow: hidden;
    box-shadow: 0 6px 18px rgba(0,0,0,.45);
  }
  .card-front {
    left: 39px; top: 394px;
    background: linear-gradient(180deg, var(--card-mid) 0%, var(--card-light) 55%, var(--card-dark) 100%);
  }
  .card-back {
    left: 623px; top: 317px;
    background: radial-gradient(ellipse at 50% 35%, var(--card-light) 0%, var(--card-mid) 45%, var(--card-dark) 100%);
  }

  .card-mark {
    position: absolute;
    font-family: "Tenor Sans", "Helvetica Neue", sans-serif;
    color: var(--brand-blue);
  }
  .card-front .card-mark { left: 30px; top: 42px; font-size: 24px; }
  .card-back .card-mark {
    left: 0; right: 0; top: 120px; text-align: center; font-size: 44px;
  }

  .company-name {
    position: absolute;
    font-family: "Tenor Sans", "Helvetica Neue", sans-serif;
    color: var(--brand-blue);
    white-space: nowrap;
  }
  .card-front .company-name { left: 151px; top: 18px; font-size: 19px; letter-spacing: 5.6px; }
  .card-back .company-name { left: 42px; top: 272px; font-size: 20px; letter-spacing: 8.4px; }

  .holder-name {
    position: absolute; right: 34px; top: 96px;
    font-size: 37px; color: var(--name-grey);
  }

  .contact-list {
    position: absolute; left: 28px; top: 155px;
    list-style: none; font-size: 19px; line-height: 24.5px;
  }
  .contact-label { color: var(--label-grey); }
  .contact-value { color: var(--value-grey); }

  .swoosh { position: absolute; left: 0; top: 0; }

  .services {
    position: absolute; left: 34px; top: 290px;
    font-size: 16px; color: var(--value-grey); white-space: nowrap;
  }
  .accreditation {
    position: absolute; left: 466px; top: 263px;
    width: 43px; height: 48px; background: var(--badge-white);
  }
</style>
</head>
<body>

  <div class="brand-showcase">
    <span class="brand-mark-dot"></span>
    <span class="brand-wordmark">Lanterra</span>
  </div>

  <section class="card card-front">
    <svg class="swoosh" width="530" height="324" viewBox="0 0 530 324" aria-hidden="true">
      <path d="M0 254 C 170 276, 400 262, 530 150 L 530 170 C 410 272, 190 284, 0 264 Z" fill="var(--swoosh-blue)"/>
      <path d="M0 264 C 190 284, 410 272, 530 170 L 530 324 L 0 324 Z" fill="var(--card-dark)" opacity=".75"/>
    </svg>
    <div class="card-mark">Lanterra</div>
    <div class="company-name">Lanterra Electrical</div>
    <div class="holder-name">Mark Delford</div>
    <ul class="contact-list">
      <li><span class="contact-label">mob:</span> <span class="contact-value">0438 517 290</span></li>
      <li><span class="contact-label">email:</span> <span class="contact-value">mrdelford@qelvo.com.au</span></li>
      <li><span class="contact-label">LIC No:</span> <span class="contact-value">TRK 540316</span></li>
    </ul>
    <div class="services">Installation &amp; Decomissioning of airconditioning Split Systems</div>
    <div class="accreditation" role="img" aria-label="Accreditation badge"></div>
  </section>

  <section class="card card-back">
    <div class="card-mark">Lanterra</div>
    <div class="company-name">Lanterra Electrical</div>
  </section>

</body>
</html>
```